Letter design, envelope design, and more

Hello, we the Tavrin Gmbh are looking for our shop. Letter C5. Design does not have to be like a business card, so it can have straight lines. Only the color is important. The logo is the text under TaVRin omit.It should not be playful but Profesionel

Font styles to use
Sans Serif

Colors
0555a3
3176b5
85abd2
85cae6
34a7d8
0792cd
cee9f5
cfdfed
000000

Requirements
Must have
• Color like business card, Please, with the text under TaVRin, Correct address Lindmattstr. 4 Zip code 9517 Goldach, as well as Couvert Without addressing only design and logo with TaVrn
Nice to have
• more writing articles
Should not have
• Not too colored, Text under TaVRin, bright colors

```html
<!DOCTYPE html>
<html lang="de">
<head>
<meta charset="utf-8">
<title>TaVRin Gmbh – Briefpapier</title>
<link rel="stylesheet" href="https://fonts.googleapis.com/css2?family=Source+Sans+3:wght@400;600&display=swap">
<style>
  :root {
    --backdrop: #b4b4b4;
    --paper: #f3f4f5;
    --ink: #222226;
    --brand-blue: #0555a3;
    --band-deep: #0555a3;
    --wave-mid: #3176b5;
    --wave-light: #85abd2;
    --footer-text: #ffffff;
  }
  * { box-sizing: border-box; margin: 0; padding: 0; }
  html, body {
    width: 1200px; height: 1072px; overflow: hidden;
    background: var(--backdrop);
    font-family: "Source Sans 3", sans-serif;
  }
  .letterhead {
    position: absolute; left: 235px; top: 20px;
    width: 730px; height: 1032px;
    background: var(--paper);
    box-shadow: 0 4px 14px rgba(0,0,0,0.25);
    overflow: hidden;
  }
  .brand {
    position: absolute; top: 52px; left: 0; right: 0;
    text-align: center;
  }
  .brand-name {
    font-size: 40px; font-weight: 600; color: var(--brand-blue);
    letter-spacing: 1px; line-height: 1;
  }
  .letter-body {
    position: absolute; left: 107px; top: 220px; width: 520px;
    color: var(--ink); font-size: 15.5px; line-height: 22px;
  }
  .salutation { font-size: 18px; margin-bottom: 38px; }
  .letter-body p.paragraph { margin-bottom: 22px; hyphens: auto; }
  .signature { margin-top: 32px; }
  .footer-waves {
    position: absolute; left: 0; bottom: 0; width: 730px; height: 170px;
  }
  .contact-row {
    position: absolute; left: 28px; right: 24px; bottom: 22px;
    display: flex; justify-content: space-between; align-items: center;
    color: var(--footer-text); font-size: 13.5px;
  }
  .contact-item { display: flex; align-items: center; gap: 6px; }
  .contact-icon { width: 19px; height: 19px; flex: none; }
  .divider { display: inline-block; width: 1px; height: 15px; background: var(--footer-text); margin: 0 5px; vertical-align: middle; }
</style>
</head>
<body>
  <main class="letterhead">
    <header class="brand">
      <div class="brand-name">TaVRin Gmbh</div>
    </header>

    <section class="letter-body">
      <p class="salutation">Dear Mr. Smith,</p>
      <p class="paragraph">Lorem ipsum dolor sit amet, consectetur adipiscing elit. Donec orci purus, luctus vitae dignissim eu, iaculis sed purus. Vivamus faucibus, ipsum nec aliquet viverra, leo mauris condimentum ligula, sit amet sagittis enim ligula quis arcu. Nam egestas tortor id nisi porttitor mattis. In tortor ante, ultricies in suscipit a, tempus non massa. Vivamus et auctor mi. Fusce vel massa nulla. Phasellus nec eros mauris, et scelerisque orci. Donec malesuada orci vitae nulla accumsan porta a id massa. Quisque accumsan iaculis magna sit amet fringilla. Maecenas consequat, magna eget tincidunt semper, odio nibh rutrum mi, id feugiat ante nisi eu risus. Vestibulum nunc orci, rhoncus a placerat in, ultricies in mi. Cras mattis varius eros, vel fringilla nisi suscipit eget.</p>
      <p class="paragraph">Quisque scelerisque sagittis nulla at porttitor. Mauris a justo et tellus interdum tristique. Sed id augue vitae urna euismod commodo aliquet a quam. Pellentesque arcu velit, cursus et malesuada ut, consequat et diam. Nullam erat sem, rhoncus id ullamcorper vitae, rhoncus et arcu. In ultricies ultricies nulla, ut rutrum nisi iaculis at. Donec eu magna a metus ornare faucibus. Fusce aliquet faucibus ultricies. Morbi semper, est id tincidunt gravida, sem arcu adipiscing lacus, ac bibendum nulla leo eu purus. Quisque nec diam sed risus consectetur a ccumsan quis quis nibh. Vestibulum id purus lorem.</p>
      <p class="signature">John Doe<br>Co-Founder &amp; CEO</p>
    </section>

    <svg class="footer-waves" viewBox="0 0 730 170" preserveAspectRatio="none" aria-hidden="true">
      <path d="M0 14 Q 380 100 730 0 L730 170 L0 170 Z" fill="var(--wave-light)"/>
      <path d="M0 20 C 250 80 500 75 730 48 L730 170 L0 170 Z" fill="var(--wave-mid)"/>
      <path d="M0 24 C 200 70 450 100 730 118 L730 170 L0 170 Z" fill="var(--band-deep)"/>
    </svg>

    <footer class="contact-row">
      <span class="contact-item">
        <svg class="contact-icon" viewBox="0 0 20 20"><circle cx="10" cy="10" r="8.5" fill="none" stroke="#fff" stroke-width="1.2"/></svg>
        www.tavrin.ch
      </span>
      <span class="contact-item">
        <svg class="contact-icon" viewBox="0 0 20 20"><circle cx="10" cy="10" r="8.5" fill="none" stroke="#fff" stroke-width="1.2"/><path d="M7 5.5l2 2-1 1.3c.6 1.3 1.6 2.3 2.9 2.9l1.3-1 2 2-1.2 1.3c-3.2-.4-6.4-3.6-6.8-6.8z" fill="none" stroke="#fff" stroke-width="1.1" stroke-linejoin="round"/></svg>
        +41 71 555 02 40
      </span>
      <span class="contact-item">
        <svg class="contact-icon" viewBox="0 0 20 20"><circle cx="10" cy="10" r="8.5" fill="none" stroke="#fff" stroke-width="1.2"/><path d="M5 10l9.5-4.5-3 9-2-3.2z M9.5 11.3l5-5.8" fill="none" stroke="#fff" stroke-width="1.1" stroke-linejoin="round"/></svg>
        info@tavrin.ch
      </span>
      <span class="contact-item">
        <svg class="contact-icon" viewBox="0 0 20 20"><circle cx="10" cy="10" r="8.5" fill="none" stroke="#fff" stroke-width="1.2"/><path d="M10 15.5s-3.6-3.8-3.6-6.3a3.6 3.6 0 0 1 7.2 0c0 2.5-3.6 6.3-3.6 6.3z" fill="none" stroke="#fff" stroke-width="1.1"/><circle cx="10" cy="9.2" r="1.2" fill="#fff"/></svg>
        <span>Lindmattstr. 4<span class="divider"></span>9517 Goldach</span>
      </span>
    </footer>
  </main>
</body>
</html>
```